Independent Financial Advisor Billboard Campaign - Maple Crest Financial

I am a local, independent financial advisor. My company is Maple Crest Financial, located in Charleston, WV. My main source of revenue comes from those nearing or entering retirement that need assistance with financial planning and investment management. Many are looking to rollover their employer retirement plan into an IRA account. I would like a billboard design campaign that focuses on this type of client. Please see our website www.maplecrestfinancial.com for more information.

```html
<!DOCTYPE html>
<html lang="en">
<head>
<meta charset="utf-8">
<title>Maple Crest Financial – Retirement Billboard</title>
<link rel="stylesheet" href="https://fonts.googleapis.com/css2?family=League+Spartan:wght@700;800&family=Montserrat:wght@500;600&display=swap">
<style>
  :root {
    --stage: #3a3a3a;
    --sky-blue: #3fa6da;
    --navy: #19467a;
    --navy-deep: #0f2f5a;
    --ink: #0b0b0b;
    --paper: #ffffff;
    --gray-top: #bdbdbd;
    --gray-bottom: #f4f4f4;
    --footer-gray: #cdcdcd;
  }
  html, body {
    margin: 0;
    width: 1200px;
    height: 1200px;
    overflow: hidden;
    background: var(--stage);
  }
  .billboard {
    position: absolute;
    left: 40px;
    top: 320px;
    width: 1120px;
    height: 560px;
    display: block;
  }
  .tagline {
    font-family: "Montserrat", sans-serif;
    font-weight: 500;
    font-size: 42px;
    fill: var(--ink);
  }
  .headline {
    font-family: "League Spartan", sans-serif;
    font-weight: 800;
  }
  .headline-top { fill: var(--ink); font-size: 134px; }
  .headline-bottom { fill: url(#navyFade); font-size: 138px; }
  .services {
    font-family: "League Spartan", sans-serif;
    font-weight: 700;
    font-size: 36px;
    fill: var(--ink);
  }
  .services .accent { fill: var(--navy); }
  .brand-name {
    font-family: "Montserrat", sans-serif;
    font-weight: 600;
    font-size: 30px;
    fill: var(--navy);
  }
  .phone-number {
    font-family: "League Spartan", sans-serif;
    font-weight: 800;
    font-size: 100px;
    fill: var(--paper);
  }
  .web-address {
    font-family: "Montserrat", sans-serif;
    font-weight: 500;
    font-size: 34px;
    fill: var(--paper);
  }
</style>
</head>
<body>
<svg class="billboard" viewBox="0 0 1120 560" xmlns="http://www.w3.org/2000/svg">
  <defs>
    <linearGradient id="panelFade" x1="0" y1="0" x2="0" y2="1">
      <stop offset="0" stop-color="var(--gray-top)"/>
      <stop offset="1" stop-color="var(--gray-bottom)"/>
    </linearGradient>
    <linearGradient id="navyFade" x1="0" y1="0" x2="0" y2="1">
      <stop offset="0" stop-color="#2b5f9c"/>
      <stop offset="1" stop-color="var(--navy-deep)"/>
    </linearGradient>
    <linearGradient id="portraitTone" x1="0" y1="0" x2="0" y2="1">
      <stop offset="0" stop-color="#c9c9c9"/>
      <stop offset="0.45" stop-color="#a9a6a8"/>
      <stop offset="1" stop-color="#223a6b"/>
    </linearGradient>
  </defs>

  <!-- main panel -->
  <rect class="main-panel" x="0" y="80" width="1120" height="322" fill="url(#panelFade)"/>
  <rect class="top-band" x="0" y="0" width="1120" height="80" fill="var(--sky-blue)"/>
  <rect class="footer-band" x="0" y="402" width="1120" height="158" fill="var(--footer-gray)"/>
  <polygon class="contact-panel" points="390,402 1120,402 1120,560 368,560" fill="var(--navy)"/>

  <!-- advisor portrait area -->
  <rect class="advisor-portrait" x="765" y="16" width="355" height="386" fill="url(#portraitTone)"
        role="img" aria-label="Portrait photo of the advisor in a navy suit and patterned tie"/>

  <text class="tagline" x="78" y="59" textLength="645" lengthAdjust="spacing">YOUR FINANCIAL FUTURE</text>

  <text class="headline headline-top" x="35" y="189" textLength="688" lengthAdjust="spacingAndGlyphs">RETIREMENT</text>
  <text class="headline headline-bottom" x="35" y="304" textLength="700" lengthAdjust="spacingAndGlyphs">DONE RIGHT</text>

  <text class="services" x="35" y="345" textLength="690" lengthAdjust="spacingAndGlyphs"><tspan class="accent">RETIREMENT</tspan> PLANNING ▪ <tspan class="accent">COLLEGE</tspan> PLANNING</text>
  <text class="services" x="231" y="383" textLength="309" lengthAdjust="spacingAndGlyphs">▪ <tspan class="accent">ESTATE</tspan> PLANNING</text>

  <!-- brand -->
  <rect class="brand-mark" x="24" y="462" width="30" height="30" fill="var(--navy)"/>
  <text class="brand-name" x="66" y="488" textLength="290" lengthAdjust="spacing">Maple Crest</text>

  <!-- phone icon -->
  <g class="phone-icon" fill="var(--paper)">
    <path d="M428 440 c-10 4 -14 14 -10 28 c6 20 20 38 38 50 c10 6 20 6 26 -2 l4 -6 c2 -3 1 -6 -2 -8 l-12 -8 c-3 -2 -6 -1 -8 1 l-4 5 c-10 -6 -18 -16 -22 -26 l5 -3 c3 -2 4 -5 3 -8 l-6 -14 c-2 -3 -5 -4 -8 -3 z"/>
    <path d="M448 446 a18 18 0 0 1 16 16" fill="none" stroke="var(--paper)" stroke-width="4" stroke-linecap="round"/>
    <path d="M450 434 a30 30 0 0 1 26 26" fill="none" stroke="var(--paper)" stroke-width="4" stroke-linecap="round"/>
  </g>

  <text class="phone-number" x="489" y="503" textLength="600" lengthAdjust="spacingAndGlyphs">304.555.0142</text>
  <text class="web-address" x="420" y="543" textLength="668" lengthAdjust="spacing">www.maplecrestfinancial.com</text>
</svg>
</body>
</html>
```